wardrobe/costume stylist needs good business card for own business

Hi:)

I'm wanting a business card for my company. I am a freelance stylist.

I do wardrobe/costume stylist to TV commercials; Films; Fashion and Lifestyle shoots.

I'd like a design based around my name Rosalind Parfrey written nicely, maybe a colour? Up to you?!

I've attached a couple of images of business cards I like
.... be creative and have fun!

Thank you :)

Reason: I was trying to get my new business card ready for before I headed overseas Friday morning but I don't think that was realistic so I'd like to extend the deadline to give time to the project. Thank you

Hi designers:) Thank you for all your designs, I've extended the deadline until Sunday, so there's a bit more time. I've attached 3 pictures of business cards which I quite like, please take a look to see if it can be of help in your process. I like the pale plain or patterned background with dark font and the dark plain or patterned background with the pale font the motifs the feminine fonts the plain fonts I like the idea of playing with a circle or some shape on one side of the card with my name or initials as in the picture I have on my post could you play around with this idea a bit please? Thank you all for the work you've done :) Rosa

Hi I am working overseas til Saturday night sorry for no feedback until I teturn Thanks :) Rosa

Hi designers, Thank you all so much for submitting your designs, I really appreciate your input into my project :) I'm sorry I didn't get to respond to some comments, and give feedback. I didn't back from being away until later than I expected, and the deadline had passed then, so apologies. Thanks to you all again for all your really good designs :) Rosa

Target Market(s)

I am a freelance stylist my target audience is producers, production companies, photographers, directors...

Industry/Entity Type

Business

Requirements
Must have
• Rosalind Parfrey
Stylist or Wardrobe Stylist

email rosaparfrey@mailbox-example.co.nz
Mobile 0218467193

(Don't have to use the words 'email' and 'mobile')
Nice to have
• Would like it to be double sided
Like B & W
Like pale colour background with dark font or white font
Like dark colour background with pale font
Should not have
• I would prefer it not to incorporate pictures

```html
<!DOCTYPE html>
<html lang="en">
<head>
<meta charset="utf-8">
<title>Rosalind Parfrey – Wardrobe Stylist business card</title>
<link rel="stylesheet" href="https://fonts.googleapis.com/css2?family=Playball&family=Arimo:wght@400;700&display=swap">
<style>
  :root {
    --page-bg: #e6e7ea;
    --denim-deep: #2d4a78;
    --denim-mid: #5f7fae;
    --denim-light: #9fb4d2;
    --tag-white: #ffffff;
    --script-red: #c3141b;
    --ink: #1d1d1f;
    --ink-soft: #3a3a3c;
    --button-dark: #1f2328;
    --button-rim: #4a4f57;
  }
  * { box-sizing: border-box; margin: 0; padding: 0; }
  html, body {
    width: 1200px; height: 480px; overflow: hidden;
    background: var(--page-bg);
  }
  .canvas {
    width: 1200px; height: 480px;
    display: flex; align-items: center; justify-content: center; gap: 48px;
  }
  .card {
    position: relative;
    width: 540px; height: 310px;
    border-radius: 6px;
    overflow: hidden;
    box-shadow: 0 4px 14px rgba(0,0,0,.18);
  }
  .denim-fill {
    position: absolute; inset: 0;
  }
  .card--front .denim-fill {
    background: radial-gradient(ellipse at 30% 60%, var(--denim-light) 0%, var(--denim-mid) 45%, var(--denim-deep) 100%);
  }
  .card--back .denim-fill {
    background: radial-gradient(ellipse at 50% 45%, var(--denim-light) 0%, var(--denim-mid) 55%, var(--denim-deep) 100%);
  }

  /* Front: white tag tucked into the pocket */
  .name-tag {
    position: absolute;
    top: 22px; right: 0;
    width: 300px; height: 150px;
    background: var(--tag-white);
    border-radius: 14px 0 0 14px;
    padding: 16px 18px 0 22px;
    box-shadow: -2px 3px 8px rgba(0,0,0,.25);
  }
  .name-script {
    font-family: "Playball", cursive;
    color: var(--script-red);
    font-weight: 400;
    line-height: 1;
  }
  .name-tag .name-script { font-size: 36px; }
  .role {
    font-family: "Arimo", sans-serif;
    font-size: 12px;
    letter-spacing: .3px;
    color: var(--ink);
    margin-top: 4px;
  }
  .contact-list {
    list-style: none;
    margin: 14px 0 0 12px;
    font-family: "Arimo", sans-serif;
    font-size: 11px;
    color: var(--ink-soft);
  }
  .contact-list li {
    display: flex; align-items: center; gap: 9px;
    margin-bottom: 8px;
  }
  .contact-icon { width: 14px; height: 14px; flex: none; }

  .pocket-button {
    position: absolute;
    border-radius: 50%;
    background: var(--button-dark);
    border: 3px solid var(--button-rim);
  }
  .card--front .pocket-button {
    width: 44px; height: 44px;
    left: 238px; top: 188px;
  }

  /* Back: pocket with button and name */
  .card--back .pocket-button {
    width: 74px; height: 74px;
    left: 233px; top: 70px;
  }
  .card--back .name-script {
    position: absolute;
    left: 0; right: 0; top: 160px;
    text-align: center;
    font-size: 46px;
  }
</style>
</head>
<body>
<main class="canvas">

  <section class="card card--front" aria-label="Card front">
    <div class="denim-fill" role="img" aria-label="Close-up photograph of a blue denim jeans pocket with stitching"></div>
    <div class="pocket-button"></div>
    <div class="name-tag">
      <h1 class="name-script">Rosalind Parfrey</h1>
      <p class="role">WARDROBE STYLIST</p>
      <ul class="contact-list">
        <li>
          <svg class="contact-icon" viewBox="0 0 14 14" aria-hidden="true">
            <rect x="1" y="3" width="12" height="8" fill="var(--script-red)"/>
            <path d="M1 3 L7 8 L13 3" fill="none" stroke="#fff" stroke-width="1.2"/>
          </svg>
          rosaparfrey@mailbox-example.co.nz
        </li>
        <li>
          <svg class="contact-icon" viewBox="0 0 14 14" aria-hidden="true">
            <rect x="4" y="1" width="6" height="12" rx="1.2" fill="none" stroke="var(--script-red)" stroke-width="1.6"/>
            <circle cx="7" cy="10.8" r=".8" fill="var(--script-red)"/>
          </svg>
          0218467193
        </li>
      </ul>
    </div>
  </section>

  <section class="card card--back" aria-label="Card back">
    <div class="denim-fill" role="img" aria-label="Photograph of a faded blue denim back pocket"></div>
    <div class="pocket-button"></div>
    <p class="name-script">Rosalind Parfrey</p>
  </section>

</main>
</body>
</html>
```